Thornbury Spa

We are a large Miami Beach spa and salon. I am still building our website but you can use it as a resource to gain a better understanding of who we are ....www.velloraspa-studio.com.

We offer a comprehensive list of services in hair, nails, massage, skin care, tanning, spray tanning and waxing and we offer high quality products for skin care, tanning and hair. We are open 7 days.

We would like to see a clean and simple menu that looks a lot like the one from "The Spa at Larkwood." In particular, we have a copy of a menu from their West Hollywood, CA location that is just beautiful. In the uploaded content you will see a sampling of that menu. We would like to see greys, blacks, silvers, whites and warm colors like reds and oranges. We specifically attempt to remain gender neutral so that we don't attract only girls (with pink colors and flowers etc). The final design should convey a simple, clean, friendly environment and the final product should be sized such that it is 1.) portable and 2.) inexpensive to print. We will be running thousands of these at a time so cost of printing is a consideration.

The booklet consists of two parts: one part is the standard menu with descriptions of services and products and photos etc (think of this as the sales piece that convinces a potential customer to visit) and will be stapled together like you would expect a small menu to be and should resemble the Larkwood menu. The prices should not be included in this part of the booklet that will be printed and stapled. The other part is a single insert and is removable and replaceable. I want this removable insert placed in the last page of the book in a folder pocket or something else that you can think of so that when it's time to change prices here that I am not throwing away all of the booklets....I am only replacing the inserts at the end of the menu booklet. Please design this single page insert so that should a customer remove it from the booklet and keep it, that it stands alone with our name, logo, website and phone number. This page can and probably will have to be 2 sided.

At the back of the booklet, I also want the polices to be printed in one page (think fine print in any sort of business dealing.)

With regard to the look and feel slider of economical v upmarket...we definitely want to convey we deliver upmarket services at reasonable prices. Think, world class services and products at reasonable, everyday prices.

With regard to the uploaded files:
I uploaded both EPS and TIF formats. The colors in those files are not the palette we want at all. The colors we want use for the circular logo must match the standard colors as depicted in the uploaded file "Thornburytanrooms"

Target Market(s)

The target market is the average 20-35 year old in Miami Beach that cares about their appearance. The range of clientele is quite diverse.

Industry/Entity Type

Environment

Requirements
Must have
• It must have elegant and simple photographs that relate to the services being offered. We are selling a service set and an environment...so this menu should be reflect that goal. The logo should be repeated often throughout the book but in subtle ways.

Stock photos are fine as long as they don't seem obviously stock.

Should not have
• Nothing buddha like. Nothing themed. It should be all inclusive and not seek to identify with any particular group or gender.

Nothing that fits the stereotype of "Miami Beach." We want to represent ourselves in the same category as the best spas in the world because we moving everything we do in that direction. Think class!

```html
<!DOCTYPE html>
<html lang="en">
<head>
<meta charset="utf-8">
<title>Thornbury Spa – Massage Menu</title>
<link rel="stylesheet" href="https://fonts.googleapis.com/css2?family=Josefin+Sans:wght@300;400&family=Open+Sans:wght@400&display=swap">
<style>
  :root {
    --bg-dark: #1e1e1f;
    --bg-mid: #3a3a3b;
    --band-grey: #8d8d8f;
    --band-grey-light: #b0b0b2;
    --heading-bar: #8a8a8c;
    --heading-bar-edge: #4a4a4c;
    --text-light: #e6e6e6;
    --text-body: #d9d9d9;
    --accent-maroon: #7a2b3e;
    --accent-maroon-dark: #5d1f2f;
    --photo-warm: #c78a9a;
  }
  * { margin: 0; padding: 0; box-sizing: border-box; }
  html, body { width: 1200px; height: 423px; overflow: hidden; background: var(--bg-dark); }
  .menu-spread {
    position: relative;
    width: 1200px;
    height: 423px;
    overflow: hidden;
    background: radial-gradient(ellipse at 70% 40%, var(--bg-mid) 0%, var(--bg-dark) 75%);
    font-family: "Open Sans", sans-serif;
  }
  .title-band {
    position: absolute;
    left: 472px; top: 22px;
    width: 728px; height: 40px;
    background: linear-gradient(90deg, var(--band-grey-light) 0%, var(--band-grey) 100%);
  }
  .menu-title {
    position: absolute;
    right: 36px; top: 14px;
    font-family: "Josefin Sans", sans-serif;
    font-weight: 300;
    font-size: 56px;
    line-height: 1;
    letter-spacing: 1px;
    color: #ffffff;
    white-space: nowrap;
  }
  .photo-panel { position: absolute; left: 0; top: 0; width: 500px; height: 423px; }
  .brand-mark {
    position: absolute;
    left: 470px; top: 126px;
    width: 64px;
    text-align: center;
    color: var(--text-light);
    font-family: "Josefin Sans", sans-serif;
    font-weight: 300;
  }
  .brand-dot {
    display: block;
    width: 20px; height: 20px;
    margin: 0 auto 5px;
    border: 1px solid var(--text-light);
    border-radius: 50%;
  }
  .brand-name { display: block; font-size: 11px; letter-spacing: 0.5px; }
  .brand-sub { display: block; font-size: 6px; letter-spacing: 4px; margin-top: 2px; }
  .service { position: absolute; width: 254px; }
  .col-left { left: 634px; }
  .col-right { left: 906px; width: 258px; }
  .service-heading {
    width: 178px; height: 11px;
    background: linear-gradient(90deg, var(--heading-bar-edge) 0 6px, var(--heading-bar) 6px);
    font-family: "Josefin Sans", sans-serif;
    font-weight: 300;
    font-size: 9.5px;
    line-height: 12px;
    letter-spacing: 0.8px;
    color: #f2f2f2;
    text-transform: uppercase;
    text-align: center;
    margin-bottom: 8px;
  }
  .service-body {
    font-size: 7.3px;
    line-height: 12.2px;
    color: var(--text-body);
    text-align: justify;
    hyphens: auto;
  }
  .swedish { top: 94px; }
  .hot-stone { top: 183px; }
  .prenatal { top: 301px; }
  .sports { top: 94px; }
  .thai { top: 284px; }
</style>
</head>
<body>
<main class="menu-spread">
  <div class="title-band"></div>
  <h1 class="menu-title">MASSAGE MENU</h1>

  <svg class="photo-panel" viewBox="0 0 500 423" role="img" aria-label="Photo of two massage tables draped in white linens scattered with red petals in a warm, candlelit treatment room">
    <defs>
      <linearGradient id="photoTone" x1="0" y1="0" x2="1" y2="1">
        <stop offset="0" stop-color="#4a1c2a"/>
        <stop offset="0.35" stop-color="#8a4a5c"/>
        <stop offset="0.65" stop-color="#c78a9a"/>
        <stop offset="1" stop-color="#e0b4bc"/>
      </linearGradient>
      <linearGradient id="bandTone" x1="0" y1="0" x2="0" y2="1">
        <stop offset="0" stop-color="#5d1f2f"/>
        <stop offset="1" stop-color="#7a2b3e"/>
      </linearGradient>
    </defs>
    <polygon points="0,0 432,0 347,423 0,423" fill="url(#photoTone)"/>
    <polygon points="432,0 478,0 390,423 347,423" fill="url(#bandTone)"/>
    <text x="0" y="0" transform="translate(88 414) rotate(-90)" font-family="Josefin Sans, sans-serif" font-weight="300" font-size="96" fill="#ffffff" fill-opacity="0.55" textLength="408" lengthAdjust="spacingAndGlyphs">MASSAGE</text>
  </svg>

  <div class="brand-mark">
    <span class="brand-dot"></span>
    <span class="brand-name">Thornbury</span>
    <span class="brand-sub">SPA</span>
  </div>

  <section class="service col-left swedish">
    <h2 class="service-heading">Swedish Massage</h2>
    <p class="service-body">A traditional massage that seeks to promote relaxation, enhance circulation and ease tension throughout the body through the use of gentle pressure. The massage may incorporate effleurage, kneading, friction or stretching, depending upon your needs.</p>
  </section>

  <section class="service col-left hot-stone">
    <h2 class="service-heading">Hot Stone Therapy</h2>
    <p class="service-body">Experience a deep sense of warmth and relaxation through the use of basalt polished over time by river currents. Our therapists warm these iron-rich stones and utilize their heat to help tense muscles relax, allowing massage therapists to manipulate your muscles more effectively. Hot stone therapy is especially effective at reducing muscular tension, relieving pain and improving circulation.</p>
  </section>

  <section class="service col-left prenatal">
    <h2 class="service-heading">Prenatal Massage</h2>
    <p class="service-body">As your pregnancy advances, your growing belly can place extra stress on your muscles and impede normal circulation. Our unique approach is designed to address your pregnancy needs and any aches and pains that may accompany it- with special attention to areas such as your lower back, buttocks and hips. By gently manipulating your skin through slow, kneading movements, our therapists will work to relieve stress and soothe sore muscles. Note: Expectant mother must be at least 20 weeks.</p>
  </section>

  <section class="service col-right sports">
    <h2 class="service-heading">Sports - Specific Massage</h2>
    <p class="service-body">Athletes, whether weekend warriors or world-class competitors, can derive significant health and performance benefits from regular sports-specific massage sessions. Sports-specific massage is a form of massage therapy that helps athletes recover from or avoid sports-related injuries, and typically utilizes more vigorous forms of massage to facilitate muscle healing or relaxation in specific areas. Sports massage therapy should be performed before and especially after a competition to prevent injuries and loss of mobility and to maximize the longevity of your sporting career. Sports-specific massages improve blood flow and nutrient delivery to your muscles, efficiently clear harmful metabolic byproducts, effectively reduce tension in your fascia, reduction of scar tissue formation, improve tissue elasticity and in your tissue's ability to absorb nutrients. It can also reduce stress experienced in and around your joints, ligaments, tendons and muscles.</p>
  </section>

  <section class="service col-right thai">
    <h2 class="service-heading">Thai Massage</h2>
    <p class="service-body">Unlike traditional massage in which you are expected to shed some clothing, Thai massage is performed with the recipient fully clothed. You are instructed to lie on a padded mat on the floor. During therapy, the practitioner may rock you, perform rhythmic muscle compression, assisted yoga positions, and stretches. Practitioners work along your energy meridians and make use of their knees, forearms, elbows, palms, and thumbs to remove knots and relieve muscle tension. The therapy can last anywhere from 30 to 90 minutes. Search for therapists and pricing in your area by visiting the National Bodywork Therapy Guild.</p>
  </section>
</main>
</body>
</html>
```